Birchline Septic Solutions

Would like to see some single sided ones but would also like to see some double sided with one sided only being the logo. Owners name is Colin Vandro. Phone number is 555-214-0387
Services are pumping, inspections, installs, and repairs

Contact Information for Business Card

555-241-0387 Colin Vandro Ashbury, OH

```html
<!DOCTYPE html>
<html lang="en">
<head>
<meta charset="utf-8">
<title>Birchline Septic Solutions — Business Cards</title>
<link href="https://fonts.googleapis.com/css2?family=Montserrat:wght@300;400;700;800&display=swap" rel="stylesheet">
<style>
  :root {
    --backdrop: #4a4a4a;
    --card-black: #161616;
    --teal: #2fbcb6;
    --white: #ffffff;
    --soft-white: #e9e9e9;
  }
  * { margin: 0; padding: 0; box-sizing: border-box; }
  html, body {
    width: 1200px; height: 801px; overflow: hidden;
    background: var(--backdrop);
    font-family: "Montserrat", sans-serif;
  }
  .sheet {
    position: relative; width: 1200px; height: 801px;
    display: flex; align-items: center; justify-content: center; gap: 40px;
  }
  .card {
    position: relative; width: 540px; height: 309px;
    background: var(--card-black); overflow: hidden;
  }

  /* Brand wordmark, one colour, one weight */
  .wordmark {
    color: var(--white); font-weight: 800; text-transform: uppercase;
    line-height: 1; text-align: center;
  }
  .wordmark__name { display: block; letter-spacing: 1px; }
  .wordmark__line { display: block; letter-spacing: 4px; margin-top: 8px; }

  /* Contact side */
  .card--contact .wordmark {
    position: absolute; left: 22px; top: 118px; width: 230px;
  }
  .card--contact .wordmark__name { font-size: 38px; }
  .card--contact .wordmark__line { font-size: 12px; }
  .divider {
    position: absolute; left: 270px; top: 58px;
    width: 1px; height: 160px; background: var(--teal);
  }
  .contact {
    position: absolute; left: 292px; top: 52px; color: var(--soft-white);
  }
  .contact__name { color: var(--teal); font-weight: 700; font-size: 22px; }
  .contact__place { font-weight: 300; font-size: 12px; margin-top: 2px; }
  .contact__list { list-style: none; margin-top: 16px; }
  .contact__item {
    display: flex; align-items: center; gap: 8px;
    font-weight: 300; font-size: 12px; line-height: 19px;
  }
  .contact__icon { width: 11px; height: 11px; flex: none; }
  .contact__address {
    font-style: normal; font-weight: 300; font-size: 12px;
    line-height: 17px; margin-top: 14px;
  }
  .swoosh { position: absolute; left: 0; bottom: 0; width: 540px; height: 309px; }

  /* Logo side */
  .card--logo .wordmark {
    position: absolute; left: 0; right: 0; top: 96px;
  }
  .card--logo .wordmark__name { font-size: 64px; }
  .card--logo .wordmark__line { font-size: 18px; letter-spacing: 7px; margin-top: 12px; }
  .services {
    position: absolute; left: 0; right: 0; bottom: 42px;
    text-align: center; color: var(--teal); font-size: 15px; font-weight: 400;
  }
</style>
</head>
<body>
<main class="sheet">

  <section class="card card--contact" aria-label="Business card, contact side">
    <div class="wordmark">
      <span class="wordmark__name">Birchline</span>
      <span class="wordmark__line">Septic Solutions</span>
    </div>

    <div class="divider"></div>

    <div class="contact">
      <p class="contact__name">Colin Vandro</p>
      <p class="contact__place">Ashbury</p>
      <ul class="contact__list">
        <li class="contact__item">
          <svg class="contact__icon" viewBox="0 0 12 12" aria-hidden="true"><path fill="#2fbcb6" d="M2.4 0.8 4 0.6 5 3.2 3.8 4.2C4.4 5.6 5.6 6.8 7 7.4L8 6.2 10.6 7.2 10.4 8.8C10.3 9.8 9.4 10.6 8.4 10.4 4.9 9.8 1.6 6.6 0.9 2.9 0.7 1.8 1.4 0.9 2.4 0.8Z"/></svg>
          555-214-0387
        </li>
        <li class="contact__item">
          <svg class="contact__icon" viewBox="0 0 12 12" aria-hidden="true"><rect x="0.5" y="2" width="11" height="8" rx="1" fill="#2fbcb6"/><path d="M1 2.6 6 6.4 11 2.6" fill="none" stroke="#161616" stroke-width="1"/></svg>
          info@youremail.com
        </li>
        <li class="contact__item">
          <svg class="contact__icon" viewBox="0 0 12 12" aria-hidden="true"><circle cx="6" cy="6" r="5.4" fill="#2fbcb6"/><path d="M0.6 6H11.4M6 0.6C3.6 3.4 3.6 8.6 6 11.4M6 0.6C8.4 3.4 8.4 8.6 6 11.4" fill="none" stroke="#161616" stroke-width="0.8"/></svg>
          www.yourwebsite.com
        </li>
      </ul>
      <address class="contact__address">Your address, City<br>State, Zip 1234</address>
    </div>

    <svg class="swoosh" viewBox="0 0 540 309" aria-hidden="true">
      <path d="M40 309 C230 304 420 288 540 256 L540 309 Z" fill="#2fbcb6"/>
      <path d="M70 300 C250 294 420 278 530 246" fill="none" stroke="#ffffff" stroke-width="2.2"/>
    </svg>
  </section>

  <section class="card card--logo" aria-label="Business card, logo side">
    <div class="wordmark">
      <span class="wordmark__name">Birchline</span>
      <span class="wordmark__line">Septic Solutions</span>
    </div>
    <p class="services">Services are pumping, inspections, installs, and repairs</p>
  </section>

</main>
</body>
</html>
```